New web design for a service provider in the medical field

We are looking for a new design for our website. We are a company that repairs and sells medical endoscopes. Our customers include doctors and hospitals. Our current website can be found at https://lumavex.de/en/lumavex-english.
We need a new web design (without programming) for the following 3 pages:
-Startpage https://lumavex.de/en/lumavex-english/
-Used endoscopes https://lumavex.de/en/used-endoscopes/
-Purchase https://lumavex.de/en/purchase/
The design should be modern and stylish.
The blue color of the logo should be reflected on the page, but not too intrusive.
I have uploaded the images from the header. If more images are needed, let me know and I will upload them.

Target Market(s)
Doctors and hospitals

```html
<!DOCTYPE html>
<html lang="en">
<head>
<meta charset="utf-8">
<title>Lumavex – Endoscope Repair</title>
<link rel="stylesheet" href="https://fonts.googleapis.com/css2?family=Jost:wght@400;500;600;700&display=swap">
<style>
:root{
  --blue:#29abe2;
  --blue-deep:#1a8fd6;
  --navy:#1f3345;
  --navy-dark:#182a3a;
  --ink:#1c2a36;
  --muted:#4a5866;
  --light:#eef4f8;
  --white:#ffffff;
}
*{box-sizing:border-box;margin:0;padding:0}
html,body{width:1200px;height:4946px;overflow:hidden}
body{font-family:"Jost",sans-serif;color:var(--ink);background:var(--white);position:relative}
.abs{position:absolute}
.accent{color:var(--blue)}
.btn{position:absolute;display:flex;align-items:center;justify-content:center;border-radius:30px;font-weight:500;text-transform:uppercase;letter-spacing:.3px}
.btn-blue{background:var(--blue);color:var(--white)}
.btn-navy{background:var(--navy);color:var(--white)}

/* header */
.site-header{position:absolute;left:0;top:0;width:1200px;height:92px;background:var(--white);z-index:3}
.logo{position:absolute;left:78px;top:0;width:180px;height:110px;border-radius:0 0 90px 90px;background:var(--white);display:flex;align-items:flex-start;justify-content:center;padding-top:30px;z-index:4}
.logo-name{font-size:26px;font-weight:600;color:var(--navy)}
.topbar{position:absolute;left:690px;top:0;width:510px;height:35px;background:var(--blue);border-radius:0 0 0 30px;color:var(--white);font-size:13px;font-weight:500;display:flex;align-items:center;gap:24px;padding-left:22px}
.topbar span{display:flex;align-items:center;gap:7px}
.topbar .dot{width:18px;height:18px;border-radius:50%;background:var(--white)}
.main-nav{position:absolute;left:302px;top:60px;display:flex;gap:28px;font-size:12px;font-weight:600;color:var(--navy);letter-spacing:.2px}
.main-nav .active{color:var(--blue-deep);border-bottom:2px solid var(--blue);padding-bottom:4px}

/* hero */
.hero{position:absolute;left:0;top:92px;width:1200px;height:710px;background:linear-gradient(100deg,#2a3c4b 0%,#23607f 38%,#1fa3e3 62%,#2bb8f2 100%)}
.hero-photo{position:absolute;left:560px;top:120px;width:640px;height:560px;background:radial-gradient(ellipse at 60% 45%,rgba(255,255,255,.55),rgba(255,255,255,0) 60%)}
.hero-kicker{left:92px;top:198px;font-size:30px;color:var(--white);font-weight:400}
.hero-title{left:92px;top:236px;font-size:40px;line-height:46px;color:var(--white);font-weight:700}
.hero .btn{left:92px;top:354px;width:192px;height:50px;font-size:15px}
.hero-curve{position:absolute;left:0;top:640px;width:1200px;height:170px}

/* intro */
.section-title{position:absolute;width:1200px;left:0;text-align:center;font-size:34px;font-weight:700;color:var(--navy);text-transform:uppercase}
.intro-text{left:180px;width:840px;top:870px;text-align:center;font-size:22px;line-height:37px;color:var(--muted)}

.about-photo{left:79px;top:1052px;width:556px;height:459px;border-radius:6px;background:linear-gradient(135deg,#f3f3f3,#dcdcdc)}
.about-box{left:586px;top:1104px;width:536px;height:364px;background:linear-gradient(135deg,#36b6ee,#1a9be0);border-radius:6px;color:var(--white);padding:44px 50px}
.about-box h2{font-size:25px;line-height:27px;font-weight:600;margin-bottom:20px}
.about-box p{font-size:13.5px;line-height:18px;margin-bottom:14px}

/* service cards */
.service-card{position:absolute;top:1580px;width:330px;height:284px;border:2px solid var(--blue);border-radius:4px;text-align:center;padding-top:28px;background:var(--white)}
.service-card.dark{background:var(--navy);border-color:var(--navy);color:var(--white)}
.service-card svg{display:block;margin:0 auto 12px}
.service-card h3{font-size:21px;font-weight:600;color:var(--navy)}
.service-card.dark h3{color:var(--white)}
.service-card .sub{font-size:17px;margin:2px 0 6px}
.service-card .desc{font-size:10.5px;line-height:16px;padding:0 34px;height:64px}
.service-card .btn{position:relative;margin:6px auto 0;width:134px;height:36px;font-size:11px}

/* faulty band */
.faulty{left:0;top:1953px;width:1200px;height:568px;background:linear-gradient(90deg,#edf4f8 0%,#e4f0f7 45%,#b9dcef 60%,#7fbfe0 100%)}
.faulty-photo{position:absolute;left:557px;top:0;width:643px;height:568px;background:linear-gradient(110deg,rgba(237,244,248,0) 0%,#9fd0ea 30%,#5aa7d3 65%,#3f85b7 100%)}
.faulty h2{position:absolute;left:132px;top:134px;font-size:32px;font-weight:700;color:var(--navy)}
.faulty h3{position:absolute;left:132px;top:196px;font-size:24px;font-weight:500;color:var(--navy)}
.faulty p{position:absolute;left:132px;top:236px;width:420px;font-size:16px;line-height:25px;color:var(--muted)}
.faulty .btn{left:132px;top:364px;width:152px;height:40px;font-size:12px}

/* features */
.feature{position:absolute;width:314px;height:240px;border:2px solid #c7e5f5;border-radius:0 40px 0 40px;padding:30px 36px}
.feature.filled{background:linear-gradient(135deg,#1c5fa9,#1d9be4);border-color:transparent;color:var(--white)}
.feature h3{font-size:18px;line-height:20px;font-weight:600;color:var(--navy);margin:14px 0 12px}
.feature.filled h3{color:var(--white)}
.feature p{font-size:14px;line-height:19px;color:var(--muted)}
.feature.filled p{color:#dbefff}

/* decision */
.decision-bg{left:0;top:3245px;width:1200px;height:790px}
.decision-title{left:0;width:1200px;top:3340px;text-align:center;font-size:26px;line-height:32px;font-weight:700;color:var(--navy);text-transform:uppercase}
.decision-rule{left:560px;top:3410px;width:80px;height:3px;background:var(--blue)}
.perk{position:absolute;width:260px}
.perk h4{font-size:14px;font-weight:600;color:var(--navy);margin-bottom:3px}
.perk p{font-size:9.5px;line-height:14px;color:var(--muted)}
.perk.left{text-align:right}
.perk-icon{position:absolute;width:50px;height:50px;border-radius:50%;background:var(--navy);border:3px solid var(--white);box-shadow:0 0 0 2px var(--blue)}
.decision-photo{left:482px;top:3494px;width:250px;height:250px;border-radius:50%;background:radial-gradient(circle at 45% 50%,#7a4a33 0%,#c99b80 30%,#e7eef3 70%)}
.decision .btn{left:486px;top:3848px;width:274px;height:44px;font-size:14px;text-transform:none;font-weight:600}

/* contact */
.contact h2{position:absolute;left:121px;top:4158px;font-size:31px;font-weight:700;color:var(--navy)}
.contact p{position:absolute;left:121px;width:440px;font-size:16px;line-height:28px;color:var(--muted)}
.contact .btn{left:127px;top:4406px;width:160px;height:42px;font-size:13px}
.contact-form{position:absolute;left:586px;top:4086px;width:482px;height:420px;background:var(--blue);border-radius:70px 0 70px 0;padding:40px 46px}
.field{height:44px;border:1px solid rgba(255,255,255,.8);color:var(--white);font-size:13px;font-weight:500;display:flex;align-items:center;gap:10px;padding-left:16px;margin-bottom:10px}
.field.area{height:78px;align-items:flex-start;padding-top:14px}
.field i{width:11px;height:11px;border-radius:50%;background:var(--white);display:block}
.submit{width:150px;height:42px;border:2px solid var(--white);border-radius:22px;color:var(--white);font-weight:700;font-size:16px;display:flex;align-items:center;justify-content:center;margin-top:12px}

/* footer */
.site-footer{position:absolute;left:0;top:4595px;width:1200px;height:351px;background:var(--navy-dark);color:var(--white)}
.footer-name{position:absolute;left:134px;top:82px;font-size:24px;font-weight:600}
.footer-about{position:absolute;left:126px;top:160px;width:290px;font-size:12.5px;line-height:15px;color:#9fb0be}
.footer-col{position:absolute;top:60px;border-left:3px solid var(--blue);padding-left:20px;height:110px}
.footer-col h5{font-size:14px;font-weight:600;margin-bottom:14px;padding-top:2px}
.footer-col li{list-style:none;font-size:14px;line-height:29px;color:#d6dee5}
.socials{display:flex;gap:6px}
.socials span{width:28px;height:28px;border-radius:50%;background:var(--white)}
.footer-divider{position:absolute;left:0;top:280px;width:1200px;height:1px;background:#34475a}
.copyright{position:absolute;left:0;top:300px;width:1200px;text-align:center;font-size:12px;color:#9fb0be}
</style>
</head>
<body>

<header class="site-header">
  <div class="logo"><span class="logo-name">Lumavex</span></div>
  <div class="topbar">
    <span><i class="dot"></i>info@lumavex.de</span>
    <span><i class="dot"></i>+49 4000 555 120-0</span>
    <span>ENG ▾</span>
  </div>
  <nav class="main-nav">
    <span class="active">ENDOSCOPE REPAIR</span>
    <span>ENDOSCOPY SYSTEMS</span>
    <span>ENDOSCOPY ACCESSORIES</span>
    <span>ACCESSORIES CATALOG</span>
    <span>PURCHASE</span>
  </nav>
</header>

<section class="hero" role="img" aria-label="Photograph of a flexible endoscope control body on a blue background">
  <div class="hero-photo"></div>
  <p class="abs hero-kicker">WELCOME TO LUMAVEX</p>
  <h1 class="abs hero-title">PUT YOUR ENDOSCOPE<br>IN RELIABLE HANDS!</h1>
  <span class="btn btn-blue">Learn more</span>
</section>
<svg class="hero-curve" viewBox="0 0 1200 170" preserveAspectRatio="none">
  <path d="M0 150 Q600 -70 1200 150 L1200 170 L0 170 Z" fill="#fff"/>
  <path d="M0 145 Q600 -75 1200 145" fill="none" stroke="#29abe2" stroke-width="6"/>
</svg>

<h2 class="section-title" style="top:808px">Your future <span class="accent">our service</span></h2>
<p class="abs intro-text">Lumavex GmbH is specialised in the repair and sale of Aurex, Kestrel and Norima flexible medical endoscopes. As a service-oriented company, we are at your side with our knowledge and skills!</p>

<div class="abs about-photo" role="img" aria-label="Photograph of two endoscope handpieces on a white surface"></div>
<div class="abs about-box">
  <h2>Endoscope repairs and second hand endoscopes from Lumavex&nbsp; cause the outcome matters!</h2>
  <p>Lumavex is a privileged partner for the start-up facility or optimisation of existing healthcare facilities, doctor's offices and hospitals. The quality and reliability of our products and our offered service are our best advertisement!</p>
  <p>As a result of optimised processes and highly qualified specialists in our company, we can work very quickly and with high quality for your benefit of least possible restrictions in your doctor's office or in your hospital.</p>
</div>

<div class="service-card" style="left:92px">
  <svg width="72" height="56" viewBox="0 0 72 56" fill="none" stroke="#29abe2" stroke-width="2.5"><circle cx="22" cy="28" r="18"/><circle cx="22" cy="28" r="10"/><path d="M22 10 H58 M58 6 v8 h10 v-8 z"/></svg>
  <h3>REPAIR</h3>
  <p class="sub">Endoscope repair service</p>
  <p class="desc">Manufacturer-independent we repair and maintain endoscopes, individual components</p>
  <span class="btn btn-blue">Learn more</span>
</div>
<div class="service-card dark" style="left:438px">
  <svg width="60" height="56" viewBox="0 0 60 56" fill="none" stroke="#29abe2" stroke-width="2.5"><path d="M14 6 h12 v14 h-12 z M20 20 v14"/><circle cx="38" cy="36" r="14"/></svg>
  <h3>SALE</h3>
  <p class="sub">Used endoscopes</p>
  <p class="desc">Our regular stock includes refurbished gastroscopes, colonoscopes, bronchoscopes, cystoscopes and duodenoscopes from the well-known manufacturers Aurex, Kestrel and Norima.</p>
  <span class="btn btn-blue">Learn more</span>
</div>
<div class="service-card" style="left:778px">
  <svg width="50" height="62" viewBox="0 0 50 62" fill="none" stroke="#29abe2" stroke-width="2.5"><path d="M16 4 h18 v18 h-18 z M12 22 h26 v14 h-26 z M25 36 v22"/></svg>
  <h3>PURCHASE</h3>
  <p class="sub">Used endoscopes</p>
  <p class="desc">We are very interested in buying your old endoscopes – even defective and dismantled! We offer fair conditions! Please contact us for a purchase offer!</p>
  <span class="btn btn-blue">Learn more</span>
</div>

<section class="abs faulty" role="img" aria-label="Photograph of a clinician in blue gloves and gown holding an endoscope">
  <div class="faulty-photo"></div>
  <h2>FAULTY <span class="accent">ENDOSCOPE?</span></h2>
  <h3>We ensure quick and smooth repairs!</h3>
  <p>Lorem ipsum dolor sit amet, consectetur adipiscing elit, sed do eiusmod tempor incididunt ut labore et dolore magna aliqua. Ut enim ad minim veniam, quis nostrud exercitation ullamco laboris n</p>
  <span class="btn btn-navy">Pick up order</span>
</section>

<h2 class="section-title" style="top:2578px;font-size:31px">Cause the <span class="accent">outcome matters</span></h2>

<div class="feature filled" style="left:132px;top:2665px">
  <svg width="44" height="44" viewBox="0 0 44 44" fill="none" stroke="#fff" stroke-width="2"><circle cx="22" cy="22" r="16"/><circle cx="22" cy="22" r="6"/></svg>
  <h3>One company for everyone</h3>
  <p>We are a service provider for doctors and hospitals!</p>
</div>
<div class="feature" style="left:461px;top:2672px">
  <svg width="50" height="50" viewBox="0 0 50 50" fill="none" stroke="#1f3345" stroke-width="2"><circle cx="25" cy="16" r="8"/><path d="M10 44 q15 -22 30 0"/></svg>
  <h3>Experience characterises us</h3>
  <p>Our team has many years of experience in the business field!</p>
</div>
<div class="feature" style="left:787px;top:2672px">
  <svg width="50" height="56" viewBox="0 0 50 56" fill="none" stroke="#29abe2" stroke-width="2"><path d="M14 4 h14 v16 h-14 z M10 20 h22 v12 h-22 z M21 32 v20"/></svg>
  <h3>The product is close to our hearts</h3>
  <p>We repair and sell second hand, flexible endoscopes!</p>
</div>
<div class="feature" style="left:141px;top:2918px">
  <svg width="44" height="50" viewBox="0 0 44 50" fill="none" stroke="#29abe2" stroke-width="2"><path d="M22 4 L40 10 V24 C40 36 22 46 22 46 C22 46 4 36 4 24 V10 Z"/><path d="M14 24 l6 6 l10 -12"/></svg>
  <h3>Guaranteed service</h3>
  <p>You receive a six-month warranty on all repairs!</p>
</div>
<div class="feature" style="left:469px;top:2924px">
  <svg width="50" height="50" viewBox="0 0 50 50" fill="none" stroke="#29abe2" stroke-width="2"><path d="M28 4 l4 8 9 1 -7 6 2 9 -8 -5 -8 5 2 -9 -7 -6 9 -1z"/><path d="M4 44 h14 q10 -8 28 -12"/></svg>
  <h3>Quality not quantity</h3>
  <p>Reliability and durability instead of inferior replacements!</p>
</div>
<div class="feature" style="left:792px;top:2926px">
  <svg width="50" height="54" viewBox="0 0 50 54" fill="none" stroke="#1f3345" stroke-width="2"><path d="M20 4 L36 10 V22 C36 34 20 42 20 42 C20 42 4 34 4 22 V10 Z"/><circle cx="34" cy="38" r="9" stroke="#29abe2"/></svg>
  <h3>Services for everyone</h3>
  <p>Our service includes the manufacturers Aurex, Kestrel and Norima!</p>
</div>

<section class="decision">
  <svg class="abs decision-bg" viewBox="0 0 1200 790" preserveAspectRatio="none">
    <path d="M0 140 Q600 -40 1200 100 L1200 620 Q600 820 0 640 Z" fill="#eef4f8"/>
    <path d="M0 130 Q600 -50 1200 90" fill="none" stroke="#29abe2" stroke-width="6"/>
    <path d="M0 650 Q600 840 1200 630" fill="none" stroke="#1f3345" stroke-width="8"/>
  </svg>
  <h2 class="abs decision-title">Lumavex GmbH, your decision<br>for your future</h2>
  <div class="abs decision-rule"></div>

  <svg class="abs" style="left:417px;top:3437px" width="380" height="380" viewBox="0 0 380 380">
    <circle cx="190" cy="182" r="176" fill="none" stroke="#29abe2" stroke-width="3"/>
  </svg>
  <div class="abs decision-photo" role="img" aria-label="Photograph of a gloved technician inspecting an endoscope tip"></div>

  <div class="perk-icon" style="left:442px;top:3494px"></div>
  <div class="perk-icon" style="left:394px;top:3606px"></div>
  <div class="perk-icon" style="left:420px;top:3729px"></div>
  <div class="perk-icon" style="left:720px;top:3491px"></div>
  <div class="perk-icon" style="left:766px;top:3606px"></div>
  <div class="perk-icon" style="left:724px;top:3729px"></div>

  <div class="perk left" style="left:154px;top:3488px"><h4>Fast Repairs</h4><p>Keep potential disruptions in your doctor's office or in your hospital at minimum</p></div>
  <div class="perk left" style="left:106px;top:3604px"><h4>On-site service</h4><p>We will gladly pay you a visit to carry out analysis and repairs on site. Due to our many years of experience</p></div>
  <div class="perk left" style="left:142px;top:3734px"><h4>Without a maintenance contract</h4><p>No subscription or other maintenance contract, but one-time and sustainable repair work</p></div>
  <div class="perk" style="left:794px;top:3488px"><h4>Highly cost efficient</h4><p>Benefit from our first class recommendations and implementation by our experienced staff.</p></div>
  <div class="perk" style="left:834px;top:3600px"><h4>Loan equipment service</h4><p>We will gladly pay you a visit to carry out analysis and repairs on site. Due to our many years of experience</p></div>
  <div class="perk" style="left:794px;top:3734px"><h4>First class service</h4><p>Our clients always come first!</p></div>

  <span class="btn btn-blue">Learn more about Lumavex</span>
</section>

<section class="contact">
  <h2>HOW CAN WE HELP YOU?</h2>
  <p style="top:4230px">Good day! We are looking forward to your message! You can get informations on possible or ongoing repairs of your endoscope technology.</p>
  <p style="top:4326px">Use the contact form below or the possibility of contacting us by post, telephone or email!</p>
  <span class="btn btn-navy">Contact us</span>
  <form class="contact-form">
    <div class="field"><i></i>First name</div>
    <div class="field"><i></i>Last name</div>
    <div class="field"><i></i>Phone number</div>
    <div class="field"><i></i>Email address</div>
    <div class="field area">Comments</div>
    <div class="submit">SUBMIT</div>
  </form>
</section>

<footer class="site-footer">
  <div class="footer-name">Lumavex</div>
  <p class="footer-about">Lorem ipsum dolor sit amet, consectetur adipiscing elit, sed do eiusmod tempor incididunt ut labore et dolore</p>
  <div class="footer-col" style="left:468px"><h5>NAVIGATION</h5><ul><li>Home</li><li>Endoscope Repair</li><li>Used Endoscope</li><li>Endoscopy Systems</li></ul></div>
  <div class="footer-col" style="left:710px"><h5>RESOURCES</h5><ul><li>Endoscopy Accessories</li><li>Purchase</li><li>Contact Us</li></ul></div>
  <div class="footer-col" style="left:918px"><h5>FOLLOW US</h5><div class="socials"><span></span><span></span><span></span><span></span></div></div>
  <div class="footer-divider"></div>
  <p class="copyright">© 2022 Lumavex GmbH</p>
</footer>

</body>
</html>
```